Print materials for 3-star hotel

We are changing up our print materials (notepads, letterheads, key card jackets, small flyer for the room rates) We are a 3 star business hotel in the Philippines and have mainly used grey tones and clean, simple lines. See attached photos for logo and hotel interior photos.

Target Market(s)

Business

Contact Information for Business Card

Corvale Terrace Hotel
Lindwell Banca Avenue corner Tolenta St Cebu City 6000 Philippines
Tel: +63 32 481 7302
Mobile: +63 917 648 2095
www.corvaleterracehotel.example

Font styles to use
Serif
Sans Serif

Requirements
Must have
• Simple
• Readable font and font size
Nice to have
• Neutral colors, grey and taupes
Should not have
• No purples and bright blues

```html
<!DOCTYPE html>
<html lang="en">
<head>
<meta charset="utf-8">
<title>Corvale Terrace Hotel — Stationery</title>
<link href="https://fonts.googleapis.com/css2?family=Marcellus&family=Montserrat:wght@400;600&display=swap" rel="stylesheet">
<style>
:root{
  --bg:#f0f0f0;
  --paper:#f7f7f7;
  --brand:#9b9b9b;
  --brand-dark:#858585;
  --text:#6e6e6e;
  --text-soft:#8a8a8a;
  --on-brand:#f4f4f4;
}
*{box-sizing:border-box;margin:0;padding:0}
html,body{width:1200px;height:1046px;overflow:hidden;background:var(--bg)}
body{position:relative;font-family:"Montserrat",sans-serif;color:var(--text)}
.piece{position:absolute;background:var(--paper);box-shadow:0 1px 3px rgba(0,0,0,.08)}
.wordmark{font-family:"Marcellus",serif;text-align:center;letter-spacing:.12em;line-height:1.1;color:var(--text-soft);text-transform:uppercase}
.wordmark .mark{display:block;margin:0 auto 5px;background:currentColor}
.wordmark small{display:block;letter-spacing:.35em;font-size:.62em}
.address{font-size:7px;text-align:center;color:var(--text)}
.band{position:absolute;left:0;right:0;bottom:0;background:var(--brand)}
.contacts{position:absolute;display:flex;justify-content:space-between;font-size:6.5px;color:var(--text-soft)}
.contacts span{display:flex;align-items:center;gap:5px;white-space:nowrap}
.contacts svg{width:11px;height:11px}

/* letterhead */
.letterhead{left:179px;top:130px;width:385px;height:544px}
.letterhead .wordmark{position:absolute;top:26px;left:0;right:0;font-size:11px}
.letterhead .wordmark .mark{width:24px;height:24px}
.letterhead .address{position:absolute;top:92px;left:0;right:0}
.letter-body{position:absolute;left:40px;right:40px;top:137px;font-size:5.6px;line-height:1.95;color:var(--text)}
.letter-body p{margin-bottom:9px;text-align:justify}
.letter-body .signer{font-weight:600;margin-bottom:10px}
.signature{width:100px;height:14px;background:linear-gradient(90deg,#cfcfcf,#e6e6e6)}
.letterhead .contacts{left:40px;right:40px;bottom:30px}
.letterhead .band{height:15px}

/* folder */
.folder{left:632px;top:106px;width:454px;height:574px;background:var(--brand)}
.folder::before{content:"";position:absolute;left:0;top:0;bottom:0;width:12px;background:var(--brand-dark);opacity:.35}
.folder .wordmark{position:absolute;top:267px;left:0;right:0;font-size:16px;color:var(--on-brand)}
.folder .wordmark .mark{width:44px;height:44px;margin-bottom:8px}

/* business cards */
.card-front{left:40px;top:724px;width:174px;height:98px}
.card-front .band{height:10px}
.card-front .mark{position:absolute;left:32px;top:21px;width:24px;height:24px;background:var(--text-soft)}
.card-front .card-address{position:absolute;left:8px;top:53px;width:72px;font-size:3.6px;line-height:1.5;text-align:center;color:var(--text)}
.card-front .divider{position:absolute;left:84px;top:17px;width:1px;height:60px;background:#cfcfcf}
.card-front .person{position:absolute;left:93px;top:19px;width:78px}
.card-front .person strong{display:block;font-size:6.3px;font-weight:600;color:var(--text)}
.card-front .person em{display:block;font-style:normal;font-size:3.8px;color:var(--text-soft);margin-bottom:7px}
.card-front .person li{list-style:none;font-size:3.6px;line-height:1.7;color:var(--text);white-space:nowrap}
.card-back{left:40px;top:850px;width:174px;height:99px;background:var(--brand)}
.card-back .wordmark{position:absolute;top:24px;left:0;right:0;font-size:8.5px;color:var(--on-brand)}
.card-back .wordmark .mark{width:24px;height:24px}

/* compliment slip */
.slip{left:260px;top:738px;width:430px;height:206px}
.slip .wordmark{position:absolute;left:20px;width:150px;top:22px;font-size:9.5px}
.slip .wordmark .mark{width:24px;height:24px}
.slip .address{position:absolute;left:34px;top:87px;text-align:left}
.slip .contacts{left:22px;width:300px;bottom:31px}
.slip .band{height:15px}

/* envelope */
.envelope{left:734px;top:738px;width:431px;height:206px}
.envelope .flap{position:absolute;left:0;top:0;width:431px;height:90px}
.envelope .wordmark{position:absolute;top:24px;left:0;right:0;font-size:9px;color:var(--on-brand)}
.envelope .wordmark .mark{width:26px;height:26px}
</style>
</head>
<body>

<svg width="0" height="0" style="position:absolute" aria-hidden="true">
  <defs>
    <symbol id="icon-phone" viewBox="0 0 12 12"><circle cx="6" cy="6" r="5.3" fill="none" stroke="#9b9b9b" stroke-width=".8"/><path d="M4.3 3.3l1 .1.4 1.3-.6.5c.3.7.8 1.2 1.5 1.5l.5-.6 1.3.4.1 1c-.3.4-.8.6-1.3.5C5.2 7.7 4.3 6.8 4 5c-.1-.6.1-1.3.3-1.7z" fill="#9b9b9b"/></symbol>
    <symbol id="icon-mail" viewBox="0 0 12 12"><circle cx="6" cy="6" r="5.3" fill="#9b9b9b"/><rect x="3.3" y="4" width="5.4" height="4" fill="none" stroke="#fff" stroke-width=".6"/><path d="M3.3 4l2.7 2 2.7-2" fill="none" stroke="#fff" stroke-width=".6"/></symbol>
    <symbol id="icon-web" viewBox="0 0 12 12"><circle cx="6" cy="6" r="5.3" fill="none" stroke="#9b9b9b" stroke-width=".8"/><circle cx="6" cy="6" r="3" fill="#9b9b9b"/></symbol>
  </defs>
</svg>

<section class="piece letterhead">
  <div class="wordmark"><span class="mark"></span>Corvale Terrace<small>Hotel</small></div>
  <p class="address">418 Halden Row, Ashvale, R2K 3P7</p>
  <div class="letter-body">
    <p>Dear Friend,</p>
    <p>Lorem ipsum dolor sit amet, consectetur adipisicing elit, sed do eiusmod tempor incididunt ut labore et dolore magna aliqua. Ut enim ad minim veniam, quis nostrud exercitation ullamco laboris nisi ut aliquip ex ea commodo consequat. Duis aute irure dolor in reprehenderit in voluptate vet nulla pariatur. Excepted est laborum.</p>
    <p>Lorem ipsum dolor sit amet, consectetur adipisicing elit, sed do eiusmod tempor incididunt ut labore et dolore magna aliqua. Ut enim ad minim veniam, quis nostrud exercitation ullamco laboris nisi ut aliquip ex ea commodo consequat. Duis t anim id est laborum. Lorem ipsum dolor sit amet, consectetur adipismodo consequat.</p>
    <p>Excepteur sint occaecat cupidatat non proident, sunt in culpa qui officia deserunt mollit anim id est laborum. Lorem ipsum dolor sit amet, consectetur adipisicing elit, sed do eiusmod oris nisi ut aliquip ex ea commodo consequat. Duis aute irure dolor in reprehenderit in voluptate velit esse cillum dolore eu fugiat nulla pari.</p>
    <p>Lorem ipsum dolor sit amet, consectetur adipisicing elit, sed do eiusmod tempor incididunt ut labore et dolore magna aliqua. Ut enim adonsequat. Duis aute irure dolor in reprehenderit in voluptate velit esse cillum dolore eu fugiat nulla pariatur.</p>
    <p>Best regards,</p>
    <p class="signer">Darien Holt</p>
    <div class="signature" role="img" aria-label="Handwritten signature"></div>
  </div>
  <div class="contacts">
    <span><svg><use href="#icon-phone"/></svg>000.000.0000</span>
    <span><svg><use href="#icon-mail"/></svg>info@corvaleterrace.example</span>
    <span><svg><use href="#icon-web"/></svg>www.corvaleterrace.example</span>
  </div>
  <div class="band"></div>
</section>

<section class="piece folder">
  <div class="wordmark"><span class="mark"></span>Corvale Terrace<small>Hotel</small></div>
</section>

<section class="piece card-front">
  <span class="mark"></span>
  <p class="card-address">Lindwell Banca Avenue corner Tolenta St, Marrowby City, 4120, Estoria</p>
  <span class="divider"></span>
  <div class="person">
    <strong>Darien HOLT</strong>
    <em>Managing Director</em>
    <ul>
      <li>+63 32 481 7302</li>
      <li>+63 917 648 2095</li>
      <li>+00 918 552 0417</li>
      <li>darien@corvaleterrace.example</li>
      <li>www.corvaleterracehotel.example</li>
    </ul>
  </div>
  <div class="band"></div>
</section>

<section class="piece card-back">
  <div class="wordmark"><span class="mark"></span>Corvale Terrace<small>Hotel</small></div>
</section>

<section class="piece slip">
  <div class="wordmark"><span class="mark"></span>Corvale Terrace<small>Hotel</small></div>
  <p class="address">418 Halden Row, Ashvale, R2K 3P7</p>
  <div class="contacts">
    <span><svg><use href="#icon-phone"/></svg>000.000.0000</span>
    <span><svg><use href="#icon-mail"/></svg>info@corvaleterrace.example</span>
    <span><svg><use href="#icon-web"/></svg>www.corvaleterrace.example</span>
  </div>
  <div class="band"></div>
</section>

<section class="piece envelope">
  <svg class="flap" viewBox="0 0 431 90" preserveAspectRatio="none" aria-hidden="true">
    <path d="M0 0H431V58L411 90H20L0 58Z" fill="#9b9b9b"/>
  </svg>
  <div class="wordmark"><span class="mark"></span>Corvale Terrace</div>
</section>

</body>
</html>
```